Website images and banners needed to be created

We have a website we have not used in a few months that need updated sales banners and images resized for our web devs to upload and update. The site in question is w w w . p a l t r o n . c o m

Number of Pages Required

3 page

```html
<!DOCTYPE html>
<html lang="en">
<head>
<meta charset="utf-8">
<title>Paltron sale banners</title>
<link rel="stylesheet" href="https://fonts.googleapis.com/css2?family=Outfit:wght@400;500;600&display=swap">
<style>
  :root {
    --page: #ffffff;
    --ink: #111111;
    --white: #ffffff;
    --yellow: #ffcc00;
    --red: #ff3b12;
    --cream: #fde8c9;
    --dark: #1f1f1f;
    --wall: #dcdad3;
    --wall-deep: #cfccc3;
    --linen: #f4f3ee;
  }
  * { margin: 0; padding: 0; box-sizing: border-box; }
  html, body { width: 1146px; height: 1200px; overflow: hidden; background: var(--page); }
  body { position: relative; font-family: "Outfit", sans-serif; color: var(--ink); }

  .banner {
    position: absolute; left: 72px; width: 1003px; height: 286px;
    overflow: hidden;
    box-shadow: 0 10px 26px rgba(0,0,0,0.12);
  }
  .banner--fabric { top: 115px; }
  .banner--family { top: 455px; background: var(--cream); }
  .banner--room { top: 796px; background: var(--dark); }

  .photo { position: absolute; }

  /* bedroom scene tones: warm grey wall, pale bed filling the lower middle, darker side tables */
  .banner--fabric .photo {
    inset: 0;
    background:
      radial-gradient(ellipse 300px 150px at 50% 100%, var(--linen) 0%, rgba(244,243,238,0.85) 55%, rgba(244,243,238,0) 100%),
      radial-gradient(ellipse 260px 90px at 50% 62%, rgba(236,235,229,0.9) 0%, rgba(236,235,229,0) 100%),
      linear-gradient(180deg, rgba(0,0,0,0) 0%, rgba(0,0,0,0) 78%, rgba(120,105,90,0.10) 100%),
      linear-gradient(90deg, #e3e2dc 0%, #e7e6e0 30%, #e4e3dd 60%, var(--wall-deep) 100%);
  }

  /* family scene tones: cream fade into warm timber wall, white bedding along the bottom */
  .banner--family .photo {
    inset: 0;
    background:
      linear-gradient(180deg, rgba(255,255,255,0) 0%, rgba(255,255,255,0) 72%, rgba(236,238,242,0.75) 100%),
      radial-gradient(ellipse 220px 160px at 82% 55%, rgba(150,150,165,0.45) 0%, rgba(150,150,165,0) 100%),
      linear-gradient(90deg, var(--cream) 0%, var(--cream) 36%, #f6d7a6 48%, #e7b56f 58%, #d9a05a 70%, #c99058 84%, #b88c66 100%);
  }

  .banner--room .photo { inset: 0; }

  .brand {
    position: absolute; font-weight: 500; font-size: 29px; line-height: 1;
    display: flex; align-items: center; gap: 12px; letter-spacing: 0.3px;
  }
  .brand__mark { width: 18px; height: 18px; background: currentColor; }

  .headline { position: absolute; font-weight: 500; font-size: 37px; line-height: 1; white-space: nowrap; }
  .copy { position: absolute; font-size: 12.5px; line-height: 16px; font-weight: 500; width: 296px; }

  .button {
    position: absolute; width: 111px; height: 34px; border-radius: 17px;
    background: var(--yellow); color: var(--ink);
    font-size: 13px; font-weight: 500; display: flex; align-items: center; justify-content: center;
  }

  /* banner 1 */
  .banner--fabric .brand { left: 0; right: 0; top: 20px; justify-content: center; }
  .banner--fabric .headline { left: 0; right: 0; top: 61px; font-size: 40px; text-align: center; text-shadow: 0 2px 3px rgba(0,0,0,0.18); }
  .banner--fabric .headline .accent { color: var(--yellow); }
  .banner--fabric .button { left: 446px; top: 109px; }

  /* banner 2 */
  .banner--family .brand { left: 90px; top: 55px; }
  .banner--family .headline { left: 90px; top: 93px; }
  .banner--family .headline .accent { color: var(--red); }
  .banner--family .copy { left: 90px; top: 140px; }
  .banner--family .button { left: 90px; top: 195px; }

  /* banner 3 */
  .banner--room .brand { left: 90px; top: 55px; color: var(--white); }
  .banner--room .headline { left: 90px; top: 93px; color: var(--yellow); }
  .banner--room .copy { left: 90px; top: 140px; color: var(--white); }
  .banner--room .button { left: 90px; top: 195px; }
</style>
</head>
<body>

<section class="banner banner--fabric">
  <div class="photo" role="img" aria-label="Bright bedroom with a white fabric bed, pillows, side tables, a plant and a lamp"></div>
  <div class="brand"><span class="brand__mark"></span>paltron.com</div>
  <h1 class="headline">Upto <span class="accent">70% Off</span> on Fabric Beds</h1>
  <a class="button">Read more</a>
</section>

<section class="banner banner--family">
  <div class="photo" role="img" aria-label="Happy family sitting together on a bed in a wooden-walled bedroom"></div>
  <div class="brand"><span class="brand__mark"></span>paltron.com</div>
  <h2 class="headline">Upto <span class="accent">70% Off</span></h2>
  <p class="copy">Contrary to popular belief, Lorem Ipsum is not simply random text. It has roots in a piece</p>
  <a class="button">Read more</a>
</section>

<section class="banner banner--room">
  <svg class="photo" width="1003" height="286" viewBox="0 0 1003 286" role="img" aria-label="Modern grey bedroom with a made bed, green throw, lamps and a potted palm">
    <defs>
      <linearGradient id="roomWall" x1="0" y1="0" x2="1" y2="0">
        <stop offset="0" stop-color="#8a8480"/>
        <stop offset="0.3" stop-color="#a7a29c"/>
        <stop offset="0.65" stop-color="#9c9894"/>
        <stop offset="1" stop-color="#6e6a62"/>
      </linearGradient>
      <linearGradient id="roomFloor" x1="0" y1="0" x2="0" y2="1">
        <stop offset="0" stop-color="#5c5a5e" stop-opacity="0"/>
        <stop offset="0.5" stop-color="#6a6f82" stop-opacity="0.65"/>
        <stop offset="1" stop-color="#55535a" stop-opacity="0.9"/>
      </linearGradient>
      <radialGradient id="roomBed" cx="0.55" cy="0.72" r="0.4">
        <stop offset="0" stop-color="#8c93ab" stop-opacity="0.7"/>
        <stop offset="1" stop-color="#8c93ab" stop-opacity="0"/>
      </radialGradient>
      <clipPath id="roomArea"><polygon points="467,0 1003,0 1003,286 548,286"/></clipPath>
    </defs>
    <g clip-path="url(#roomArea)">
      <rect x="0" y="0" width="1003" height="286" fill="url(#roomWall)"/>
      <rect x="0" y="100" width="1003" height="186" fill="url(#roomFloor)"/>
      <rect x="467" y="0" width="536" height="286" fill="url(#roomBed)"/>
    </g>
  </svg>
  <div class="brand"><span class="brand__mark"></span>paltron.com</div>
  <h2 class="headline">Upto 70% Off</h2>
  <p class="copy">Contrary to popular belief, Lorem Ipsum is not simply random text. It has roots in a piece</p>
  <a class="button">Read more</a>
</section>

</body>
</html>
```